Start-Up für Training, Coaching & Consulting sucht modernes Webdesign!
Zielgruppe
Wer ist TAVI Training, Coaching & Consulting?
Wir führen Führungskräftetrainings durch, machen Privatkunden für Bewerbungen fit und unterstützen Unternehmen mit Verkaufstrainings. Wir entwickeln Persönlichkeiten im Coaching. Wir beraten Unternehmen und helfen ihnen dabei, ihre Geschäftsabläufe und Prozesse zu optimieren. Dabei steht unsere hohe Qualität im Mittelpunkt - gemeinsam mit unseren kreativen Trainingsmethoden. Unser Background (Diplom-Kaufleute und geprüfte Trainer) bietet dafür die passende Ausgangslage.
Was bedeutet TAVI?
Tavi ist Maori und bdeutet Kreis/Spirale. Er symbolisiert einen wachsenden Silberfarn und steht für persönliche Entwicklung und Entfaltung. Der Tavi ist einerseits unser Namensgeber und unser Logo, andererseits steht der Tavi aber auch für unsere Werte: Denn wir wollen unseren Kunden dabei helfen zu wachsen und sich weiterzuentwickeln - und dies auf eine hochqualitative und seriöse Art und Weise ohne den Eindruck von Esoterik oder Erlebnispädagogik zu vermitteln.
Aufgabenstellung
Modernes Design, das unsere Philosophie widerspiegelt: Wir möchten unseren Kunden auf seriöse und hochqualitative Weise weiterentwickeln. Wir stehen für nachhaltigen Lernerfolg, kreative Trainingsmethoden, Abwechslung, Spaß am Lernen, Qualität, Kompetenz, Fachwissen und Dynamik.
Layout:
1) Header: QMSR geprüfter Trainer, Menüpunkte (siehe Architektur)
2) Banner
3) 3 Teaser (Training, Coaching, Consulting) + Header + 2-3 Zeilen Text (+Icons)
>>> Sichtbarer Bereich auf Homepage: Menü, Banner, Teaser
4) "Warum Sie uns wählen sollten": 5 bullet points ohne weiteren Text
5) "Aus unserem Blog": Frame für 3 Blogartikel + Bild + Datum + Header + 2-3 Zeilen Text
6) Alle drei QMSR Logos
7) Footer: Click Us (quick links), Contact Us (Adresse), Follow Us (Pinnwald, ZOLP, Kontaktor)
8) Copyright + Impressum
>>> Das Design soll klar sein, aber nicht zu kantig. Vielmehr sollen abgerundete Ecken und dynamische Elemente genutzt werden.
Architektur:
3 Ebenen:
1) Homepage
2) TAVI, Training, Coaching, Consulting, für Trainer, Kundenstimmen/Referenzen, Kontakt
3) noch zu bestimmende Produktdetailseiten
Texte werden noch erstellt, Layout kann ggf. mit Platzhaltertext gefüllt werden.
Bildmaterial: Logo und vorhandenes Imagebild werden zur Verfügung gestellt. Bilder können ggf. gekauft werden. Vorschläge erwünscht.
Corporate colors:
grün: #a2c61b + monochromatic colors
http://www.tintoskop.de/a2c61b
grau: #474747 + monochromatic colors
http://www.tintoskop.de/474747

```html
<!DOCTYPE html>
<html lang="de">
<head>
<meta charset="utf-8">
<title>TAVI – Training, Coaching &amp; Consulting</title>
<link href="https://fonts.googleapis.com/css2?family=Open+Sans:wght@400;600;700&display=swap" rel="stylesheet">
<style>
:root{
  --green:#a2c61b;
  --green-light:#cfe383;
  --green-dark:#7d9a12;
  --grey:#474747;
  --grey-dark:#2b2b2b;
  --text:#222;
  --white:#fff;
}
*{box-sizing:border-box;margin:0;padding:0}
html,body{width:849px;height:1200px;overflow:hidden}
body{position:relative;background:var(--white);font-family:"Open Sans",sans-serif;color:var(--text)}
.abs{position:absolute}

/* header */
.site-header{left:0;top:0;width:849px;height:56px;background:var(--white)}
.brand{left:44px;top:12px;display:flex;align-items:center;gap:6px}
.brand-dot{width:18px;height:18px;border-radius:50%;background:var(--green)}
.brand-name{font-weight:700;font-size:24px;color:var(--grey);letter-spacing:1px;line-height:1}
.brand-sub{left:44px;top:42px;font-size:5.5px;color:var(--grey)}
.cert-badge{left:193px;top:17px;width:82px;height:22px;display:flex;gap:2px}
.cert-badge span{background:#1f6fb8;height:100%}
.main-nav{top:22px;font-weight:700;font-size:11.5px;color:var(--grey)}
.main-nav.active{color:var(--green)}
.header-rule{left:0;top:56px;width:849px;height:6px;background:linear-gradient(90deg,var(--green-light),var(--green) 40%)}

/* hero */
.hero{left:0;top:62px;width:849px;height:324px;background:radial-gradient(ellipse at 45% 35%,#8cc63a 0%,#4f8f1f 35%,#2a5a14 65%,#1c3d0d 100%)}
.hero-title{left:132px;top:139px;font-size:19px;line-height:22px;color:var(--white);font-weight:400}
.hero-btn{left:133px;top:213px;width:89px;height:29px;border-radius:15px;background:var(--green);font-size:7px;font-weight:700;color:var(--grey-dark);display:flex;align-items:center;justify-content:center}
.hero-arrow{top:160px;width:32px;height:32px;border-radius:50%;background:var(--green)}

/* teaser cards */
.card{top:288px;width:226px;height:400px;background:var(--white);border-radius:22px 22px 0 0;box-shadow:0 0 10px rgba(0,0,0,.15)}
.card-fade{left:0;top:560px;width:849px;height:140px;background:linear-gradient(180deg,rgba(255,255,255,0),var(--white) 85%)}
.card-img{top:308px;width:181px;height:92px}
.accent-line{left:0;top:418px;width:849px;height:5px;background:linear-gradient(90deg,var(--green-light),var(--green) 30%)}
.icon-badge{top:392px;width:52px;height:52px;border-radius:50%;background:var(--white);box-shadow:0 1px 4px rgba(0,0,0,.25);display:flex;align-items:center;justify-content:center}
.icon-badge span{width:44px;height:44px;border-radius:50%;background:var(--green)}
.card-title{top:457px;width:226px;text-align:center;font-size:12.5px;font-weight:600;color:var(--green);letter-spacing:.3px}
.card-text{top:481px;width:180px;font-size:8.6px;line-height:13.6px}
.more{font-size:8.6px;font-weight:600;color:var(--green);display:flex;align-items:center;gap:4px}
.more i{display:inline-block;width:7px;height:7px;border-radius:50%;background:var(--green)}

/* reasons */
.section-title{top:638px;font-size:19px;font-weight:600;color:var(--grey-dark)}
.reason{left:108px;display:flex;align-items:center;gap:16px;font-size:16px;color:var(--green)}
.reason svg{width:19px;height:19px}

/* blog */
.blog-img{left:463px;width:94px;height:77px;border-radius:3px}
.blog-body{left:585px;width:175px}
.blog-date{font-size:7.5px;color:var(--grey-dark)}
.blog-heading{font-size:12.5px;color:var(--green);line-height:15px}
.blog-text{font-size:7.3px;line-height:10.4px;color:#666}
.blog-body .more{font-size:7.3px;font-weight:700}
.blog-body .more i{width:6px;height:6px}

/* memberships */
.member{top:1016px;height:22px;background:#1f6fb8}

/* footer */
.footer-rule{left:0;top:1079px;width:849px;height:6px;background:linear-gradient(90deg,var(--green-light),var(--green) 40%)}
.site-footer{left:0;top:1085px;width:849px;height:115px;background:var(--grey-dark)}
.footer-brand{left:89px;top:1110px;display:flex;align-items:center;gap:6px}
.footer-brand .brand-name{color:var(--white)}
.footer-brand-sub{left:89px;top:1141px;font-size:5.5px;color:#ccc}
.footer-col{top:1106px;color:var(--white);font-size:9.5px;font-weight:600;line-height:12.5px}
.footer-col h3{font-size:12.5px;color:var(--green);font-weight:600;margin-bottom:7px}
.social{display:flex;align-items:center;gap:8px}
.social i{display:inline-block;width:7px;height:7px;border-radius:50%;background:var(--white)}
</style>
</head>
<body>

<header class="abs site-header"></header>
<div class="abs brand"><span class="brand-dot"></span><span class="brand-name">TAVI</span></div>
<div class="abs brand-sub">Training · Coaching · Consulting</div>
<div class="abs cert-badge" aria-label="Zertifikat geprüfter Trainer"><span style="width:16px"></span><span style="width:64px"></span></div>
<nav>
  <div class="abs main-nav active" style="left:367px">LEISTUNGEN ●</div>
  <div class="abs main-nav" style="left:473px">ÜBER UNS</div>
  <div class="abs main-nav" style="left:556px">FÜR TRAINER ⌄</div>
  <div class="abs main-nav" style="left:666px">REFERENZEN</div>
  <div class="abs main-nav" style="left:766px">KONTAKT</div>
</nav>
<div class="abs header-rule"></div>

<section class="abs hero" role="img" aria-label="Nahaufnahme eines sich entrollenden Farnwedels"></section>
<h1 class="abs hero-title">Lernen und Wissen<br>vermitteln:<br>Leicht gemacht</h1>
<div class="abs hero-btn">MEHR ERFAHREN</div>
<svg class="abs hero-arrow" style="left:44px" viewBox="0 0 32 32"><circle cx="16" cy="16" r="16" fill="#a2c61b"/><path d="M18.5 9 L11.5 16 L18.5 23" stroke="#2b2b2b" stroke-width="3.5" fill="none" stroke-linecap="round"/></svg>
<svg class="abs hero-arrow" style="left:772px" viewBox="0 0 32 32"><circle cx="16" cy="16" r="16" fill="#a2c61b"/><path d="M13.5 9 L20.5 16 L13.5 23" stroke="#2b2b2b" stroke-width="3.5" fill="none" stroke-linecap="round"/></svg>

<div class="abs card" style="left:45px"></div>
<div class="abs card" style="left:312px"></div>
<div class="abs card" style="left:578px"></div>
<div class="abs card-fade"></div>

<div class="abs card-img" style="left:67px;background:linear-gradient(180deg,#6a9cc4 0%,#e9c98a 45%,#c27a2e 65%,#3c3a2a 100%)" role="img" aria-label="Straße durch Hügel im Sonnenuntergang"></div>
<div class="abs card-img" style="left:333px;height:94px;background:radial-gradient(ellipse at 50% 60%,#9bd04a,#4f8f1f 60%,#234a10)" role="img" aria-label="Junger Farnwedel"></div>
<div class="abs card-img" style="left:600px;background:linear-gradient(180deg,#d9d9d9 0%,#9c9c9c 55%,#3a3a3a 100%)" role="img" aria-label="Person sitzt auf einem Felsvorsprung über Bergen"></div>

<div class="abs accent-line"></div>
<div class="abs icon-badge" style="left:134px"><span></span></div>
<div class="abs icon-badge" style="left:398px"><span></span></div>
<div class="abs icon-badge" style="left:665px"><span></span></div>

<h2 class="abs card-title" style="left:45px">TRAINING</h2>
<h2 class="abs card-title" style="left:312px">COACHING</h2>
<h2 class="abs card-title" style="left:578px">CONSULTING</h2>

<div class="abs card-text" style="left:68px">Durch mich gebiert das Netz die Kunst aus sich selbst heraus. Nicht schlicht reproduk­tiver Natur, repräsentiere ich vielmehr die kontinuierliche Evolution des Wortes.<div class="more">mehr <i></i></div></div>
<div class="abs card-text" style="left:334px">Durch mich gebiert das Netz die Kunst aus sich selbst heraus. Nicht schlicht reproduk­tiver Natur, repräsentiere ich vielmehr die kontinuierliche Evolution des Wortes.<div class="more">mehr <i></i></div></div>
<div class="abs card-text" style="left:602px">Durch mich gebiert das Netz die Kunst aus sich selbst heraus. Nicht schlicht reproduk­tiver Natur, repräsentiere ich vielmehr die kontinuierliche Evolution des Wortes.<div class="more">mehr <i></i></div></div>

<h2 class="abs section-title" style="left:101px">Warum Sie uns wählen sollten</h2>
<div class="abs reason" style="top:688px"><svg viewBox="0 0 20 20"><circle cx="10" cy="10" r="10" fill="#a2c61b"/><path d="M8 5.5 L12.5 10 L8 14.5" stroke="#2b2b2b" stroke-width="2.4" fill="none"/></svg>Grund Nummer Eins</div>
<div class="abs reason" style="top:749px"><svg viewBox="0 0 20 20"><circle cx="10" cy="10" r="10" fill="#a2c61b"/><path d="M8 5.5 L12.5 10 L8 14.5" stroke="#2b2b2b" stroke-width="2.4" fill="none"/></svg>Grund Nummer Zwei</div>
<div class="abs reason" style="top:811px"><svg viewBox="0 0 20 20"><circle cx="10" cy="10" r="10" fill="#a2c61b"/><path d="M8 5.5 L12.5 10 L8 14.5" stroke="#2b2b2b" stroke-width="2.4" fill="none"/></svg>Grund Nummer Drei</div>
<div class="abs reason" style="top:874px"><svg viewBox="0 0 20 20"><circle cx="10" cy="10" r="10" fill="#a2c61b"/><path d="M8 5.5 L12.5 10 L8 14.5" stroke="#2b2b2b" stroke-width="2.4" fill="none"/></svg>Grund Nummer Vier</div>
<div class="abs reason" style="top:937px"><svg viewBox="0 0 20 20"><circle cx="10" cy="10" r="10" fill="#a2c61b"/><path d="M8 5.5 L12.5 10 L8 14.5" stroke="#2b2b2b" stroke-width="2.4" fill="none"/></svg>Grund Nummer Fünf</div>

<h2 class="abs section-title" style="left:586px">Aus unserem Blog</h2>

<div class="abs blog-img" style="top:683px;background:linear-gradient(135deg,#c9a477,#6b5a4a 55%,#2e2a27)" role="img" aria-label="Person arbeitet am Laptop auf einem Holztisch"></div>
<article class="abs blog-body" style="top:681px">
  <div class="blog-date">02.02.2016</div>
  <div class="blog-heading">Heading 01</div>
  <p class="blog-text">Durch mich gebiert das Netz die Kunst aus sich selbst heraus. Nicht schlicht reproduktiver Natur, repräsentiere ich vielmehr die kontinuierliche Evolution des Wortes.</p>
  <div class="more">mehr <i></i></div>
</article>

<div class="abs blog-img" style="top:788px;background:linear-gradient(160deg,#7fa9ad,#4f7a80 55%,#5c6a5a)" role="img" aria-label="Person in Yogapose auf einem Felsen über dem Meer"></div>
<article class="abs blog-body" style="top:785px">
  <div class="blog-date">09.02.2016</div>
  <div class="blog-heading">Heading 02</div>
  <p class="blog-text">Durch mich gebiert das Netz die Kunst aus sich selbst heraus. Nicht schlicht reproduktiver Natur, repräsentiere ich vielmehr die kontinuierliche Evolution des Wortes.</p>
  <div class="more">mehr <i></i></div>
</article>

<div class="abs blog-img" style="top:889px;background:linear-gradient(160deg,#5a3a2a,#b9763d 55%,#8d5a2e)" role="img" aria-label="Besprechung an einem Holztisch mit Tablet und Kaffee"></div>
<article class="abs blog-body" style="top:887px">
  <div class="blog-date">14.02.2016</div>
  <div class="blog-heading">Heading 03</div>
  <p class="blog-text">Durch mich gebiert das Netz die Kunst aus sich selbst heraus. Nicht schlicht reproduktiver Natur, repräsentiere ich vielmehr die kontinuierliche Evolution des Wortes.</p>
  <div class="more">mehr <i></i></div>
</article>

<div class="abs member" style="left:316px;width:17px" aria-label="Mitgliedschaft"></div>
<div class="abs member" style="left:373px;width:17px" aria-label="Berufsverband"></div>
<div class="abs member" style="left:443px;width:85px;border-radius:2px" aria-label="Geprüfter Trainer"></div>

<div class="abs footer-rule"></div>
<footer class="abs site-footer"></footer>
<div class="abs footer-brand"><span class="brand-dot"></span><span class="brand-name">TAVI</span></div>
<div class="abs footer-brand-sub">Training · Coaching · Consulting</div>

<div class="abs footer-col" style="left:239px"><h3>Click Us</h3>Link Title Number 1<br>Link Title Number 2<br>Link Title Number 3</div>
<div class="abs footer-col" style="left:398px"><h3>Contact Us</h3>Tavi GmbH<br>Lindenweg 14<br>34127 Feldbach<br>Germany</div>
<div class="abs footer-col" style="left:560px"><h3>Follow Us</h3>
  <div class="social"><i></i>Pinnwald</div>
  <div class="social"><i></i>ZOLP</div>
  <div class="social"><i></i>Kontaktor</div>
</div>
<div class="abs footer-col" style="left:690px"><h3>Impressum</h3>© 2016 TAVI</div>

</body>
</html>
```